Kentucky residential recovery center needs a flyer design

We need a flyer design for a 16 bed male residential/inpatient recovery center based in Richmond, Kentucky. The facility provides short term (average 30 day) treatment to those struggling with substace abuse and addiction. The design should communicate trust, assurance, safety.
Our wesite provides more information https://corvalmend.org/treatment-services/residential-treatment/

Target Market(s)

Men (typically 30-50) struggling with substance addiction

```html
<!DOCTYPE html>
<html lang="en">
<head>
<meta charset="utf-8">
<title>Corvalmend Health – Residential Recovery Flyer</title>
<link rel="stylesheet" href="https://fonts.googleapis.com/css2?family=Montserrat:ital,wght@0,500;0,600;0,700;1,800;1,900&family=Lato:wght@400&display=swap">
<style>
  :root{
    --navy:#262a5a;
    --sky:#6db6e6;
    --white:#ffffff;
    --stage:#cccccc;
    --wood:#8a7a68;
    --room:#b9a98f;
  }
  *{box-sizing:border-box;margin:0;padding:0}
  html,body{width:1200px;height:1200px;overflow:hidden;background:var(--stage)}
  .flyer{position:absolute;left:193px;top:40px;width:814px;height:1120px;background:var(--white);font-family:"Lato",sans-serif;color:var(--navy)}
  .band{position:absolute;left:0;width:100%}

  /* header */
  .header{top:0;height:200px;background:var(--navy)}
  .brand{position:absolute;left:35px;top:38px;width:134px;height:134px;border-radius:50%;background:var(--white);display:flex;align-items:center;justify-content:center;text-align:center}
  .brand-name{font-family:"Montserrat",sans-serif;font-weight:700;font-size:15px;line-height:1.25;color:var(--navy);letter-spacing:.5px}
  .headline{position:absolute;left:210px;top:84px;font-family:"Montserrat",sans-serif;font-style:italic;font-weight:900;font-size:29.5px;line-height:27px;color:var(--white);text-transform:uppercase;letter-spacing:-.2px}

  /* stats */
  .stats{top:200px;height:195px;background:var(--sky);display:flex;padding:39px 0 38px}
  .stat{flex:none;text-align:center;position:relative;padding:0 22px}
  .stat + .stat{border-left:2px solid var(--white)}
  .stat:nth-child(1){width:228px}
  .stat:nth-child(2){width:213px}
  .stat:nth-child(3){width:189px}
  .stat:nth-child(4){width:184px}
  .stat-figure{font-family:"Montserrat",sans-serif;font-style:italic;font-weight:900;font-size:29px;line-height:1;color:var(--navy)}
  .stat-label{font-family:"Montserrat",sans-serif;font-style:italic;font-weight:800;font-size:11.5px;line-height:16px;text-transform:uppercase;margin-top:10px}
  .stat-note{font-size:8.3px;line-height:11px;color:var(--white);text-align:left;position:absolute;left:22px;right:12px;top:82px}
  .stat:nth-child(1) .stat-figure{margin-top:-4px}
  .stat:nth-child(1) .stat-note{top:86px;left:44px;right:30px}
  .stat:nth-child(3) .stat-note{right:60px}
  .stat:nth-child(2) .stat-figure,.stat:nth-child(3) .stat-figure{margin-top:12px}
  .stat:nth-child(4) .stat-figure{margin-top:8px}
  .stat:nth-child(4) .stat-label{margin-top:6px;line-height:19px}

  /* services */
  .services{top:395px;height:377px;background:var(--white)}
  .services-title{position:absolute;left:0;top:23px;display:flex;align-items:center;font-family:"Montserrat",sans-serif;font-weight:500;font-size:14.3px;letter-spacing:.4px;text-transform:uppercase}
  .services-title::before{content:"";width:20px;height:23px;background:var(--sky);margin-right:6px}
  .service-list{position:absolute;left:49px;top:63px;list-style:none}
  .service-list li{height:24.8px;display:flex;align-items:center;font-family:"Montserrat",sans-serif;font-weight:600;font-variant:small-caps;font-size:16px;letter-spacing:1.3px}
  .service-list li::before{content:"";width:14px;height:14px;margin-right:15px;background:var(--navy)}
  .service-list li:nth-child(even)::before{background:var(--sky)}
  .gallery-main{position:absolute;left:447px;top:0;width:367px;height:276px;background:linear-gradient(160deg,#d8cdbd 0%,var(--room) 45%,var(--wood) 100%)}
  .gallery-thumb{position:absolute;top:276px;height:101px}
  .thumb-a{left:447px;width:101px;background:linear-gradient(170deg,#c9bda9,#6f6356)}
  .thumb-b{left:548px;width:129px;background:linear-gradient(170deg,#b59a74,#5a4a3c)}
  .thumb-c{left:677px;width:137px;background:linear-gradient(170deg,#c6b493,#5b4b3e)}

  /* stories */
  .stories{top:772px;height:245px;background:var(--navy)}
  .portrait{position:absolute;top:12px;width:209px;height:219px}
  .portrait-a{left:14px;background:linear-gradient(180deg,#8fb2d0,#3f4576 55%,#c0555f)}
  .portrait-b{left:238px;background:linear-gradient(180deg,#4d8ad6,#9aa4b0 60%,#6d7077)}
  .program{position:absolute;left:480px;width:320px;color:var(--white)}
  .program h3{font-family:"Montserrat",sans-serif;font-weight:600;font-size:10.2px;letter-spacing:.6px;text-transform:uppercase;line-height:13px}
  .program p{font-size:8.3px;line-height:11.2px;max-width:305px}
  .program-1{top:29px}
  .program-1 p{max-width:272px}
  .program-2{top:97px}
  .program-3{top:159px}
  .program-3 p{font-size:10px;line-height:12px;max-width:320px}

  /* footer */
  .footer{top:1017px;height:103px;background:var(--sky);color:var(--white)}
  .contact{position:absolute;display:flex;align-items:center;gap:14px}
  .contact svg{flex:none;fill:var(--navy)}
  .contact-email{left:48px;top:20px;font-size:9.5px}
  .contact-phone{left:282px;top:20px;font-size:13.5px}
  .contact-address{left:487px;top:18px;align-items:flex-start;gap:22px;font-size:9.3px;line-height:12px}
  .contact-address p + p{margin-top:7px}
</style>
</head>
<body>
<main class="flyer">

  <header class="band header">
    <div class="brand"><span class="brand-name">Corvalmend<br>Health</span></div>
    <h1 class="headline">Kentuckys Leading Drug &amp;<br>Alcohol Addiction Treatment</h1>
  </header>

  <section class="band stats">
    <div class="stat">
      <div class="stat-figure">#1</div>
      <div class="stat-label">Best Drug &amp;<br>Alcohol Rehab Center</div>
      <p class="stat-note">Voted one of the best Alcohol and Drug rehab centers</p>
    </div>
    <div class="stat">
      <div class="stat-figure">2,500+</div>
      <div class="stat-label">Patients Treated</div>
      <p class="stat-note">Over 2,500 patients treated successfully and counting</p>
    </div>
    <div class="stat">
      <div class="stat-figure">100+</div>
      <div class="stat-label">Years</div>
      <p class="stat-note">Over 100 years of medical and clinical experience behind our team</p>
    </div>
    <div class="stat">
      <div class="stat-figure">95%</div>
      <div class="stat-label">Satisfaction<br>Rating</div>
      <p class="stat-note">Our patients rate us 95 out of 100</p>
    </div>
  </section>

  <section class="band services">
    <h2 class="services-title">Below is a summary of services offered by us:</h2>
    <ul class="service-list">
      <li>Outpatient</li>
      <li>Inpatient/Residential</li>
      <li>Intensive Outpatient</li>
      <li>Targeted Case Management</li>
      <li>Peer Support</li>
      <li>Individual and Group Therapy</li>
      <li>Medicated Assisted Treatment</li>
      <li>(‘MAT’)</li>
      <li>Relovane, Buprenorphine &amp; Naltrevia</li>
      <li>Treatment</li>
      <li>Physician Appointments</li>
      <li>Telemedicine</li>
    </ul>
    <div class="gallery-main" role="img" aria-label="Photo of a resident bedroom with a sofa, bunk beds and wood floor"></div>
    <div class="gallery-thumb thumb-a" role="img" aria-label="Photo of a bedroom with bunk beds and a round table"></div>
    <div class="gallery-thumb thumb-b" role="img" aria-label="Photo of a lounge with leather sofas and a rug"></div>
    <div class="gallery-thumb thumb-c" role="img" aria-label="Photo of a living area with a leather sofa and wall art"></div>
  </section>

  <section class="band stories">
    <div class="portrait portrait-a" role="img" aria-label="Photo of a program graduate holding his certificate of completion outside the center"></div>
    <div class="portrait portrait-b" role="img" aria-label="Photo of a bearded program graduate holding his certificate of completion"></div>
    <article class="program program-1">
      <h3>Inpatient/Residential</h3>
      <p>Residential treatment for addiction is a type of inpatient treatment that provides 24/7 care and support for individuals struggling with addiction. Residential treatment programs typically last for 30-90 days.</p>
    </article>
    <article class="program program-2">
      <h3>Intensive Outpatient Program (IOP)</h3>
      <p>Intensive outpatient programs (IOPs) take place more often than typical outpatient programs—usually 9 hours or more of treatment per week for 3 to 5 days.</p>
    </article>
    <article class="program program-3">
      <h3>Outpatient</h3>
      <p>Outpatient substance abuse treatment is a form of rehabilitation in which people are treated on a part-time basis<br>(usually 1-2 hours/week).</p>
    </article>
  </section>

  <footer class="band footer">
    <div class="contact contact-email">
      <svg width="28" height="28" viewBox="0 0 24 24" aria-hidden="true"><path d="M12 2a10 10 0 1 0 5.2 18.5l-1-1.7A8 8 0 1 1 20 12v1.2a1.8 1.8 0 0 1-3.6 0V7.5h-2v.9A4.9 4.9 0 1 0 15 16a3.8 3.8 0 0 0 7-2.8V12A10 10 0 0 0 12 2zm0 13a3 3 0 1 1 0-6 3 3 0 0 1 0 6z"/></svg>
      <span>ADMISSIONS@CORVALMEND.ORG</span>
    </div>
    <div class="contact contact-phone">
      <svg width="26" height="26" viewBox="0 0 24 24" aria-hidden="true"><path d="M6.6 10.8a15.1 15.1 0 0 0 6.6 6.6l2.2-2.2a1 1 0 0 1 1-.25 11.4 11.4 0 0 0 3.6.57 1 1 0 0 1 1 1V20a1 1 0 0 1-1 1A17 17 0 0 1 3 4a1 1 0 0 1 1-1h3.5a1 1 0 0 1 1 1c0 1.25.2 2.45.57 3.57a1 1 0 0 1-.25 1z"/></svg>
      <span>859-555-0142</span>
    </div>
    <div class="contact contact-address">
      <svg width="20" height="28" viewBox="0 0 20 28" aria-hidden="true"><path d="M10 0a10 10 0 0 0-10 10c0 7.5 10 18 10 18s10-10.5 10-18A10 10 0 0 0 10 0zm0 14a4 4 0 1 1 0-8 4 4 0 0 1 0 8z"/></svg>
      <div>
        <p>ADDRESS (CENTRAL KY CLINIC)<br>1410 &amp; 1412 Maple Ridge Drive, Richmond, Kentucky 40475</p>
        <p>ADDRESS (NORTHERN KY CLINIC)<br>2280 Commerce Park Way, Burlington, Kentucky 41005</p>
      </div>
    </div>
  </footer>

</main>
</body>
</html>
```